Business card

We need a business card design for our company based in Auckland , New Zealand called 'Ridge + Studio Ltd'. We provide architectural services. We would like to see designs that use the max. three colours (such as white, black, grey) The final design should communicate financial safety and growth."
Also I will provide our company logo. I would like to the logo to be embeded onto our business card.

Target Market(s)

new residential house, alteration & addition & light commericila design & drafting service

Industry/Entity Type

Architecture

Contact Information for Business Card

Company name: ridge + studio Ltd.
Name: Mark Delford
Job title: architectural designer & Design LBP
email address: mark@rplusd.co.nz
mobile number: 02 5163 2290
web site: www.rplusd.co.nz

Requirements
Must have
• My project must have..
• - embeded logo (attached company logo)
• I don't have a bigger version for our company logo, but I have one old one, so you can remove the word from it)
• - insert the attached small BKTW logo & LBP logo
• - creative, simple and clear business card.
• - Max. three colours
Nice to have
• - Here are the samples I would like to share with you: http://www.plimvora.com/blog/minimalistic-business-card-designs/
• I would like to have my business card like one of the creation.
Should not have
• TBA

```html
<!DOCTYPE html>
<html lang="en">
<head>
<meta charset="utf-8">
<title>Ridge + Studio Ltd — Business Card</title>
<link rel="stylesheet" href="https://fonts.googleapis.com/css2?family=Source+Sans+3:wght@400;600;700&family=PT+Sans+Narrow&display=swap">
<style>
  :root {
    --backdrop: #3b3b3b;
    --paper: #ffffff;
    --ink: #111111;
    --grey: #8a8a8a;
    --text: #333333;
    --badge-ring: #9a9a9a;
  }
  * { box-sizing: border-box; margin: 0; padding: 0; }
  html, body {
    width: 1105px; height: 1200px; overflow: hidden;
    background: var(--backdrop);
    font-family: "Source Sans 3", Arial, sans-serif;
  }
  .canvas { position: relative; width: 1105px; height: 1200px; }

  .card {
    position: absolute; left: 207px; width: 690px; height: 412px;
  }
  .card--front { top: 170px; background: var(--paper); }
  .card--back  { top: 628px; background: var(--ink); }

  /* Front */
  .brand-mark {
    position: absolute; right: 44px; top: 96px;
    display: flex; align-items: center; gap: 12px;
  }
  .brand-mark__dot {
    width: 22px; height: 22px; border-radius: 50%; background: var(--ink);
  }
  .brand-mark__name {
    font-size: 26px; font-weight: 600; color: var(--ink); letter-spacing: 0.5px;
  }
  .holder { position: absolute; left: 47px; top: 182px; }
  .holder__name {
    font-size: 26px; font-weight: 700; color: var(--ink); letter-spacing: 0.5px; line-height: 1;
  }
  .holder__title {
    font-family: "PT Sans Narrow", Arial, sans-serif;
    font-size: 19px; color: var(--grey); margin-top: 8px;
  }
  .holder__company { font-size: 19px; color: var(--text); margin-top: 18px; }
  .contacts { list-style: none; margin-top: 14px; }
  .contacts li {
    display: flex; align-items: center; gap: 14px;
    font-size: 18px; color: var(--text); height: 27px;
  }
  .contacts svg { width: 18px; height: 18px; fill: var(--ink); flex: none; }

  /* Back */
  .back-mark {
    position: absolute; left: 0; right: 0; top: 150px;
    display: flex; justify-content: center; align-items: center; gap: 16px;
  }
  .back-mark__dot { width: 30px; height: 30px; border-radius: 50%; background: var(--paper); }
  .back-mark__name { font-size: 38px; font-weight: 600; color: var(--paper); letter-spacing: 1px; }
  .back-web {
    position: absolute; left: 0; right: 0; top: 358px; text-align: center;
    font-size: 19px; color: var(--paper);
  }
  .partner {
    position: absolute; left: 28px; top: 318px;
    font-size: 36px; font-weight: 700; color: var(--paper); letter-spacing: 1px;
  }
  .lbp-badge {
    position: absolute; left: 552px; top: 284px; width: 108px; height: 108px;
    border-radius: 50%; background: var(--paper); border: 8px solid var(--badge-ring);
  }
</style>
</head>
<body>
<main class="canvas">
  <section class="card card--front">
    <div class="brand-mark">
      <span class="brand-mark__dot"></span>
      <span class="brand-mark__name">ridge + studio</span>
    </div>
    <div class="holder">
      <h1 class="holder__name">MARK DELFORD</h1>
      <p class="holder__title">architectural designer &amp; Design LBP</p>
      <p class="holder__company">ridge + studio Ltd.</p>
      <ul class="contacts">
        <li>
          <svg viewBox="0 0 16 16" aria-hidden="true"><path d="M4 0h8a1 1 0 0 1 1 1v14a1 1 0 0 1-1 1H4a1 1 0 0 1-1-1V1a1 1 0 0 1 1-1zm1 2v10h6V2z"/></svg>
          02 5163 2290
        </li>
        <li>
          <svg viewBox="0 0 16 16" aria-hidden="true"><path d="M1 3h14v10H1zM2 4.2v.6l6 4 6-4v-.6z"/></svg>
          mark@rplusd.co.nz
        </li>
        <li>
          <svg viewBox="0 0 16 16" aria-hidden="true"><circle cx="8" cy="8" r="7.5"/><path d="M4 5c2 0 3 1 2 3s1 3 0 5M10 2c-1 2 1 3 3 3M11 9c1 1 2 1 3 0" stroke="#fff" stroke-width="1.2" fill="none"/></svg>
          www.rplusd.co.nz
        </li>
      </ul>
    </div>
  </section>

  <section class="card card--back">
    <div class="back-mark">
      <span class="back-mark__dot"></span>
      <span class="back-mark__name">ridge + studio</span>
    </div>
    <p class="partner">BKTW</p>
    <p class="back-web">www.rplusd.co.nz</p>
    <div class="lbp-badge" role="img" aria-label="Licensed practitioner certification badge"></div>
  </section>
</main>
</body>
</html>
```